Business Card Design Project

We need a Business Card for an Mechanical Engineering firm in Singapore. The design should be Modern & Technical looking, yet eye catching.

Our company deals in Cutting Tools & Machine Accessories for the Manufacturing Industries such as Oil & Gas, Aero Space, etc... For more information on our Company, you can either email me or view our website www.torvalen.com.sg.

We are trying to revamp our image to give our consumers a fresh new perspective to our company, so we welcome all ideas.

Industry/Entity Type

Business

Requirements
Must have
• Must incorporate New Company Logo into the card as shown in Uploaded file.

```html
<!DOCTYPE html>
<html lang="en">
<head>
<meta charset="utf-8">
<title>Torvalen Tools – Business Card</title>
<link rel="stylesheet" href="https://fonts.googleapis.com/css2?family=Arimo:wght@400;700&display=swap">
<style>
  :root {
    --crimson: #9c1636;
    --crimson-deep: #8a1230;
    --paper: #f2f1f0;
    --paper-shade: #e4e2e1;
    --pill: rgba(255, 255, 255, 0.22);
    --ink-light: #ffffff;
    --ink-soft: #f6dde3;
    --backdrop: #e9e7e5;
  }
  * { box-sizing: border-box; margin: 0; padding: 0; }
  html, body { width: 1200px; height: 900px; overflow: hidden; }
  body {
    background: var(--backdrop);
    font-family: "Arimo", Arial, sans-serif;
    position: relative;
  }
  .card {
    position: absolute;
    left: 270px;
    width: 660px;
    height: 396px;
    border-radius: 6px;
    overflow: hidden;
    box-shadow: 0 6px 18px rgba(0, 0, 0, 0.18);
    background: var(--crimson);
  }

  /* Back face */
  .card--back { top: 40px; }
  .back-panel {
    position: absolute;
    left: 0; top: 0;
    width: 560px;
    height: 396px;
    background: linear-gradient(160deg, var(--paper), var(--paper-shade));
    border-radius: 0 210px 210px 0 / 0 198px 198px 0;
  }
  .back-brand {
    position: absolute;
    left: 150px;
    top: 150px;
    display: flex;
    align-items: center;
    gap: 12px;
  }
  .brand-dot {
    width: 34px; height: 34px;
    border-radius: 50%;
    background: var(--crimson);
  }
  .brand-name {
    color: var(--crimson);
    font-weight: 700;
    font-size: 34px;
    letter-spacing: 1px;
  }
  .back-web {
    position: absolute;
    left: 160px;
    top: 214px;
    color: var(--crimson);
    font-size: 15px;
    letter-spacing: 0.3px;
  }

  /* Front face */
  .card--front { top: 464px; background: linear-gradient(180deg, var(--crimson), var(--crimson-deep)); }
  .front-tab {
    position: absolute;
    left: 0; top: 0;
    width: 262px; height: 112px;
    background: var(--paper);
    border-radius: 0 0 44px 0;
    display: flex;
    align-items: center;
    justify-content: center;
    gap: 8px;
  }
  .front-tab .brand-dot { width: 20px; height: 20px; }
  .front-tab .brand-name { font-size: 20px; letter-spacing: 0.5px; }

  .pill {
    position: absolute;
    left: 0;
    background: var(--pill);
  }
  .pill--contact { top: 124px; width: 318px; height: 66px; border-radius: 0 22px 22px 0; }
  .pill--address { top: 198px; width: 430px; height: 72px; border-radius: 0 26px 26px 0; }
  .pill--web { top: 278px; width: 300px; height: 34px; border-radius: 0 17px 17px 0; }

  .row {
    position: absolute;
    left: 44px;
    display: flex;
    align-items: center;
    gap: 8px;
    color: var(--ink-light);
    font-size: 13px;
    letter-spacing: 0.4px;
  }
  .icon { width: 13px; height: 13px; flex: none; }

  .address {
    position: absolute;
    left: 44px;
    top: 208px;
    color: var(--ink-light);
    font-size: 13px;
    line-height: 1.3;
    letter-spacing: 0.3px;
    display: flex;
    gap: 8px;
  }
  .address strong { font-weight: 700; }

  .name-tag {
    position: absolute;
    right: 0;
    top: 196px;
    width: 190px;
    height: 52px;
    background: var(--pill);
    border-radius: 26px 0 0 26px;
    padding: 8px 0 0 24px;
    color: var(--ink-light);
  }
  .name-tag .person { font-weight: 700; font-size: 18px; letter-spacing: 0.5px; }
  .name-tag .role { font-size: 12px; color: var(--ink-soft); letter-spacing: 0.6px; margin-top: 2px; }
</style>
</head>
<body>

  <section class="card card--back" aria-label="Business card, back">
    <div class="back-panel"></div>
    <div class="back-brand">
      <span class="brand-dot"></span>
      <span class="brand-name">TORVALEN TOOLS</span>
    </div>
    <p class="back-web">Website: hello@torvalen.com.sg</p>
  </section>

  <section class="card card--front" aria-label="Business card, front">
    <div class="front-tab">
      <span class="brand-dot"></span>
      <span class="brand-name">TORVALEN TOOLS</span>
    </div>

    <div class="pill pill--contact"></div>
    <div class="pill pill--address"></div>
    <div class="pill pill--web"></div>

    <div class="row" style="top:128px">
      <svg class="icon" viewBox="0 0 16 16"><circle cx="8" cy="8" r="8" fill="#fff"/><path d="M5 4h2l1 2.5-1.2 1a5 5 0 0 0 2.7 2.7l1-1.2L13 10v2a1 1 0 0 1-1 1A8 8 0 0 1 4 5a1 1 0 0 1 1-1z" fill="#9c1636" transform="scale(.8) translate(2 2)"/></svg>
      <span>Tel: 65-61234570</span>
    </div>
    <div class="row" style="top:147px">
      <svg class="icon" viewBox="0 0 16 16"><circle cx="8" cy="8" r="8" fill="#fff"/><rect x="4" y="6" width="8" height="5" rx="1" fill="#9c1636"/><rect x="5.5" y="3.5" width="5" height="3" fill="#9c1636"/></svg>
      <span>Fax: 65-61234571</span>
    </div>
    <div class="row" style="top:166px">
      <svg class="icon" viewBox="0 0 16 16"><circle cx="8" cy="8" r="8" fill="#fff"/><path d="M4.5 8.2l2.3 2.3 4.7-4.8" stroke="#9c1636" stroke-width="1.8" fill="none"/></svg>
      <span>Email: hello@torvalen.com.sg</span>
    </div>

    <div class="address">
      <svg class="icon" viewBox="0 0 16 16"><circle cx="8" cy="8" r="8" fill="#fff"/><path d="M8 3.5l4.5 4H11v4.5H5V7.5H3.5z" fill="#9c1636"/></svg>
      <div>
        <strong>Torvalen Tools Pte Ltd</strong><br>
        27 Kallang Way #03-12, Meridian Industrial Hub,<br>
        Singapore 349241
      </div>
    </div>

    <div class="row" style="top:287px">
      <svg class="icon" viewBox="0 0 16 16"><circle cx="8" cy="8" r="8" fill="#fff"/><circle cx="8" cy="8" r="4.5" fill="none" stroke="#9c1636" stroke-width="1.3"/><path d="M3.5 8h9M8 3.5v9" stroke="#9c1636" stroke-width="1"/></svg>
      <span>Website: hello@torvalen.com.sg</span>
    </div>

    <div class="name-tag">
      <div class="person">Melissa</div>
      <div class="role">Designation</div>
    </div>
  </section>

</body>
</html>
```